Law Firm Header Revision

Task: Redesign my law firm Word document header (modern, succinct, logo-first, easy address updates)

I need you to revise and modernize my Microsoft Word document header for Law Office of Bram Holcott, PLLC. The result should look professional and clean on letters (including Letters of Protection), with the logo as the main focus and the text kept succinct.

Goals:
1. Create a modern, minimal header that feels premium and uncluttered.
Make the logo the most visually dominant element.
Reduce the visual weight of the contact/address block so it doesn’t distract from the document.
Make the address easy to change later (I’m moving offices soon) while keeping the same header design.

2. Content to include (keep all info accurate):
Law Office of Bram Holcott, PLLC
615 Pemberly St. Ste #300-214, Houston, TX 77002
Office: 832.555.0143
Direct: 713.555.0187
Fax: 832.555.0129
Bholcottlaw.com

3. Layout requirements:
Provide 3 header style options:
Logo left + contact info right
Centered logo + single concise contact line below
Logo left + firm name prominent + minimal contact line
The primary line near the logo should be minimal (preferably website + main office phone).
The address should be easy to update in one place without redesigning the header. Prefer either:
Move the full address to the footer, or
Put the address in a single dedicated line/block so I can edit it once and keep the layout unchanged.
4. Build constraints:
Must be achievable using standard Microsoft Word tools only (header/footer, tables, alignment, fonts, spacing). No advanced graphics software.
Provide exact header text, plus step-by-step Word instructions for each option:
Font recommendations + sizes
Alignment
Spacing
Table setup (if used)
How to keep it consistent across pages

5. Deliverable:
For each of the 3 options, provide:
The exact header content (with line breaks)
Formatting specs (fonts, sizes, spacing)
Word build steps so I can recreate it reliably and keep the logo as the focal point.

```html
<!DOCTYPE html>
<html lang="en">
<head>
<meta charset="utf-8">
<title>Law Office of Bram Holcott, PLLC — Letterhead Options</title>
<link href="https://fonts.googleapis.com/css2?family=Open+Sans:wght@400;600&family=Josefin+Sans:wght@400&display=swap" rel="stylesheet">
<style>
  :root {
    --navy: #0b1424;
    --backdrop: #5f5f5f;
    --paper: #ffffff;
    --ink: #1d1d1f;
    --on-navy: #ffffff;
  }
  * { margin: 0; padding: 0; box-sizing: border-box; }
  html, body { width: 1200px; height: 4471px; overflow: hidden; background: var(--backdrop); }
  body { position: relative; font-family: "Open Sans", Arial, sans-serif; color: var(--ink); }

  .letterhead {
    position: absolute; left: 52px; width: 1096px; height: 1419px;
    background: var(--paper); border-top: 2px solid var(--navy);
  }
  .option-1 { top: 57px; }
  .option-2 { top: 1528px; }
  .option-3 { top: 2999px; }

  .brand { position: absolute; display: flex; align-items: center; gap: 14px; }
  .brand-mark { width: 60px; height: 60px; background: var(--navy); }
  .brand-name {
    font-family: "Open Sans", Arial, sans-serif; font-weight: 600; font-size: 30px;
    color: var(--navy); letter-spacing: 1px; line-height: 1;
  }
  .brand-left { left: 50px; top: 24px; }
  .brand-center { left: 50%; transform: translateX(-50%); top: 20px; }

  .firm-name { position: absolute; left: 50px; top: 104px; font-size: 17px; }

  .contact-tabs { position: absolute; top: 0; }
  .tab-text {
    position: absolute; display: flex; align-items: center; gap: 10px;
    color: var(--on-navy); font-size: 17px; height: 40px;
  }
  .tab-text svg { width: 16px; height: 16px; fill: var(--on-navy); }

  .contact-line {
    position: absolute; top: 106px; left: 0; width: 100%;
    display: flex; justify-content: center; align-items: center; gap: 20px; font-size: 17px;
  }
  .contact-item { display: flex; align-items: center; gap: 14px; }

  .icon-dot {
    width: 38px; height: 38px; border-radius: 50%; background: var(--navy);
    display: flex; align-items: center; justify-content: center; flex-shrink: 0;
  }
  .icon-dot svg { width: 17px; height: 17px; fill: var(--on-navy); }

  .footer-contacts { position: absolute; top: 1303px; left: 0; width: 100%; height: 38px; font-size: 17px; }
  .footer-contacts .contact-item { position: absolute; top: 0; height: 38px; }
  .fax { left: 66px; }
  .address { left: 327px; }
  .direct { left: 886px; }

  .footer-bar {
    position: absolute; bottom: 0; left: 0; width: 100%; height: 52px; background: var(--navy);
    color: var(--on-navy); font-family: "Josefin Sans", Arial, sans-serif; font-size: 19px;
    display: flex; align-items: center; justify-content: center; padding-top: 3px; letter-spacing: .3px;
  }
</style>
</head>
<body>

<!-- Shared icon symbols -->
<svg width="0" height="0" style="position:absolute">
  <defs>
    <symbol id="i-globe" viewBox="0 0 24 24"><path d="M12 2a10 10 0 1 0 0 20 10 10 0 0 0 0-20zm6.9 6h-3a15 15 0 0 0-1.4-4 8 8 0 0 1 4.4 4zM12 4c.9 1.2 1.6 2.5 2 4h-4c.4-1.5 1.1-2.8 2-4zM4.3 14a8 8 0 0 1 0-4h3.4a16 16 0 0 0 0 4zm.8 2h3a15 15 0 0 0 1.4 4A8 8 0 0 1 5.1 16zm3-8h-3a8 8 0 0 1 4.4-4 15 15 0 0 0-1.4 4zM12 20c-.9-1.2-1.6-2.5-2-4h4c-.4 1.5-1.1 2.8-2 4zm2.3-6H9.7a14 14 0 0 1 0-4h4.6a14 14 0 0 1 0 4zm.2 6a15 15 0 0 0 1.4-4h3a8 8 0 0 1-4.4 4zm1.8-6a16 16 0 0 0 0-4h3.4a8 8 0 0 1 0 4z"/></symbol>
    <symbol id="i-phone" viewBox="0 0 24 24"><path d="M6.6 10.8a15.1 15.1 0 0 0 6.6 6.6l2.2-2.2a1 1 0 0 1 1-.25 11.4 11.4 0 0 0 3.6.57 1 1 0 0 1 1 1V20a1 1 0 0 1-1 1A17 17 0 0 1 3 4a1 1 0 0 1 1-1h3.5a1 1 0 0 1 1 1c0 1.25.2 2.45.57 3.57a1 1 0 0 1-.25 1z"/></symbol>
    <symbol id="i-pin" viewBox="0 0 24 24"><path d="M12 2a7 7 0 0 0-7 7c0 5.2 7 13 7 13s7-7.8 7-13a7 7 0 0 0-7-7zm0 9.5A2.5 2.5 0 1 1 12 6.5a2.5 2.5 0 0 1 0 5z"/></symbol>
    <symbol id="i-fax" viewBox="0 0 24 24"><path d="M7 2h8l3 3v4h2a2 2 0 0 1 2 2v9a2 2 0 0 1-2 2H4a2 2 0 0 1-2-2v-9a2 2 0 0 1 2-2h1V2zm2 2v5h7V6h-2V4zM6 13v2h2v-2zm4 0v2h2v-2zm4 0v2h4v-2zm-8 4v2h2v-2zm4 0v2h2v-2zm4 0v2h4v-2z"/></symbol>
  </defs>
</svg>

<!-- Option 1: Logo left + contact tabs right -->
<section class="letterhead option-1">
  <div class="brand brand-left"><span class="brand-mark"></span><span class="brand-name">BRAM HOLCOTT LAW</span></div>
  <svg class="contact-tabs" width="1096" height="44" viewBox="0 0 1096 44">
    <polygon points="544,0 799,0 778,42 565,42" fill="var(--navy)"/>
    <polygon points="811,0 1011,0 990,42 790,42" fill="var(--navy)"/>
  </svg>
  <div class="tab-text" style="left:584px;top:1px"><svg><use href="#i-globe"/></svg>Bholcottlaw.com</div>
  <div class="tab-text" style="left:830px;top:1px"><svg><use href="#i-phone"/></svg>832.555.0143</div>

  <div class="footer-contacts">
    <div class="contact-item fax"><span class="icon-dot"><svg><use href="#i-fax"/></svg></span>832.555.0129</div>
    <div class="contact-item address"><span class="icon-dot"><svg><use href="#i-pin"/></svg></span>615 Pemberly St. Ste #300-214, Houston, TX 77002</div>
    <div class="contact-item direct"><span class="icon-dot"><svg><use href="#i-phone"/></svg></span>713.555.0187</div>
  </div>
  <footer class="footer-bar">Copyright© 2026 Law Office of Bram Holcott, PLLC</footer>
</section>

<!-- Option 2: Centered logo + single contact line -->
<section class="letterhead option-2">
  <div class="brand brand-center"><span class="brand-mark"></span><span class="brand-name">BRAM HOLCOTT LAW</span></div>
  <div class="contact-line">
    <div class="contact-item"><span class="icon-dot"><svg><use href="#i-globe"/></svg></span>Bholcottlaw.com</div>
    <div class="contact-item"><span class="icon-dot"><svg><use href="#i-phone"/></svg></span>832.555.0143</div>
  </div>

  <div class="footer-contacts">
    <div class="contact-item fax"><span class="icon-dot"><svg><use href="#i-fax"/></svg></span>832.555.0129</div>
    <div class="contact-item address"><span class="icon-dot"><svg><use href="#i-pin"/></svg></span>615 Pemberly St. Ste #300-214, Houston, TX 77002</div>
    <div class="contact-item direct"><span class="icon-dot"><svg><use href="#i-phone"/></svg></span>713.555.0187</div>
  </div>
  <footer class="footer-bar">Copyright© 2026 Law Office of Bram Holcott, PLLC</footer>
</section>

<!-- Option 3: Logo left + firm name + minimal contact tab -->
<section class="letterhead option-3">
  <div class="brand brand-left"><span class="brand-mark"></span><span class="brand-name">BRAM HOLCOTT LAW</span></div>
  <p class="firm-name">Law Office of Bram Holcott, PLLC</p>
  <svg class="contact-tabs" width="1096" height="44" viewBox="0 0 1096 44">
    <polygon points="622,0 1046,0 1024,42 644,42" fill="var(--navy)"/>
    <line x1="847" y1="10" x2="847" y2="32" stroke="#5a6272" stroke-width="1"/>
  </svg>
  <div class="tab-text" style="left:664px;top:1px"><svg><use href="#i-globe"/></svg>Bholcottlaw.com</div>
  <div class="tab-text" style="left:874px;top:1px"><svg><use href="#i-phone"/></svg>832.555.0143</div>

  <div class="footer-contacts">
    <div class="contact-item fax"><span class="icon-dot"><svg><use href="#i-fax"/></svg></span>832.555.0129</div>
    <div class="contact-item address"><span class="icon-dot"><svg><use href="#i-pin"/></svg></span>615 Pemberly St. Ste #300-214, Houston, TX 77002</div>
    <div class="contact-item direct"><span class="icon-dot"><svg><use href="#i-phone"/></svg></span>713.555.0187</div>
  </div>
  <footer class="footer-bar">Copyright© 2026 Law Office of Bram Holcott, PLLC</footer>
</section>

</body>
</html>
```